Harborline Auto LLC

Car Dealer Customer Service
Address: 2874 Cresthaven Road, Shelbyville, TN 37162
web: www.harborlineautoxq.net
email: harborlineautoxq@mailnest.example
Phone: (931) 555-0148
Phone: (629) 555-0173

```html
<!DOCTYPE html>
<html lang="en">
<head>
<meta charset="utf-8">
<title>Harborline Auto – Business Card</title>
<link href="https://fonts.googleapis.com/css2?family=Montserrat:wght@400;500;800&display=swap" rel="stylesheet">
<style>
  :root {
    --brand-blue: #2a8fcc;
    --brand-blue-deep: #1f78b4;
    --brand-yellow: #ebb43f;
    --ink: #1b1b1b;
    --paper: #ffffff;
    --backdrop: #e9e9eb;
  }
  * { margin: 0; padding: 0; box-sizing: border-box; }
  html, body {
    width: 1200px; height: 900px; overflow: hidden;
    background: var(--backdrop);
    font-family: "Montserrat", sans-serif;
  }
  .canvas { position: relative; width: 1200px; height: 900px; }
  .card {
    position: absolute; left: 285px; width: 630px; height: 360px;
    background: var(--paper);
    box-shadow: 0 6px 18px rgba(0,0,0,0.12);
    overflow: hidden;
  }
  .card--front { top: 70px; }
  .card--back { top: 470px; }

  .wordmark {
    position: absolute; display: flex; align-items: center; gap: 14px;
  }
  .wordmark__dot {
    width: 26px; height: 26px; border-radius: 50%;
    background: var(--brand-blue); flex: none;
  }
  .wordmark__name {
    font-weight: 800; color: var(--brand-blue-deep);
    text-transform: uppercase; letter-spacing: 1px; white-space: nowrap;
  }
  .card--front .wordmark { left: 50%; top: 50%; transform: translate(-50%, -50%); }
  .card--front .wordmark__name { font-size: 36px; }
  .card--back .wordmark { left: 30px; top: 152px; gap: 10px; }
  .card--back .wordmark__dot { width: 20px; height: 20px; }
  .card--back .wordmark__name { font-size: 20px; letter-spacing: 0.5px; }

  .divider {
    position: absolute; left: 318px; top: 62px; width: 2px; height: 190px;
    background: var(--brand-blue);
  }
  .contact {
    position: absolute; left: 338px; top: 50px; color: var(--ink);
    font-size: 13px; line-height: 18px; font-weight: 500;
  }
  .contact__role { margin-bottom: 4px; }
  .contact__address { margin-bottom: 10px; }
  .contact__list { list-style: none; }
  .contact__item { display: flex; align-items: center; gap: 8px; height: 21px; white-space: nowrap; }
  .contact__item svg { width: 13px; height: 13px; flex: none; fill: var(--brand-blue); }
  .contact__email { font-size: 12px; }
  .contact__highlight { color: var(--brand-blue); }

  .stripes { position: absolute; left: 0; bottom: 0; width: 630px; height: 90px; }
</style>
</head>
<body>
<main class="canvas">

  <section class="card card--front" aria-label="Card front">
    <div class="wordmark">
      <span class="wordmark__dot"></span>
      <span class="wordmark__name">Harborline Auto</span>
    </div>
  </section>

  <section class="card card--back" aria-label="Card back">
    <div class="wordmark">
      <span class="wordmark__dot"></span>
      <span class="wordmark__name">Harborline Auto</span>
    </div>

    <div class="divider"></div>

    <div class="contact">
      <p class="contact__role">Car Dealer Customer Service</p>
      <p class="contact__address">2874 Cresthaven Road,<br>Shelbyville, TN 37162</p>
      <ul class="contact__list">
        <li class="contact__item">
          <svg viewBox="0 0 16 16" aria-hidden="true"><path d="M3.6 1.5l2.3 2.9-1.4 1.6c.9 2 2.4 3.6 4.5 4.6l1.6-1.4 2.9 2.3-1.2 2.5C7 13.6 2.4 9 1.5 3z"/></svg>
          (931) 555-0148
        </li>
        <li class="contact__item">
          <svg viewBox="0 0 16 16" aria-hidden="true"><path d="M1 5c3-3 11-3 14 0l-2 2-2.5-1V4.5h-5V6L3 7z"/><rect x="3.5" y="8" width="9" height="6" rx="1"/></svg>
          (629) 555-0173
        </li>
        <li class="contact__item contact__email">
          <svg viewBox="0 0 16 16" aria-hidden="true"><path d="M1 3h14v1.2L8 9 1 4.2z"/><path d="M1 5.8l7 4.8 7-4.8V13H1z"/></svg>
          harborlineautoxq@mailnest.example
        </li>
        <li class="contact__item">
          <svg viewBox="0 0 16 16" aria-hidden="true"><circle cx="8" cy="8" r="7"/><path d="M1 8h14M8 1c-3 3.5-3 10.5 0 14M8 1c3 3.5 3 10.5 0 14" stroke="#fff" stroke-width="1" fill="none"/></svg>
          <span>www.<span class="contact__highlight">harborlineautoxq</span>.net</span>
        </li>
      </ul>
    </div>

    <svg class="stripes" viewBox="0 0 630 90" aria-hidden="true">
      <polygon points="0,50 410,50 404,58 0,58" fill="var(--brand-blue)"/>
      <polygon points="0,64 400,64 382,90 0,90" fill="var(--brand-yellow)"/>
      <polygon points="430,22 630,22 630,90 398,90" fill="var(--brand-blue)"/>
    </svg>
  </section>

</main>
</body>
</html>
```